Business cards for a fun web development agency

Hi,I am building a web development agency. You can read about it on the website http://kite-loft.examplehost.com. Basically, I want to focus on free and open source products and stay as far away from the corporate business feeling as possible. I want to build a community so I want the business card to feel fun and approachable (at the risk of professional if need be). I am uploading some of my image assets in various file formats. Feel free to use them or make your own if you want just keeping in theme with the website.
Industry/Entity Type
Building
Contact Information for Business Card
Company Name: Boat ShedWebsite: www.kiteloftdev.example (it's currently in alpha on http://kite-loft.examplehost.com if you want to see the them we are trying to capture)My name is: Banner B. SchaferMy email: banner@boatsheddev.comMy phone: 0431 587 904
Look and feel

```html
<!DOCTYPE html>
<html lang="en">
<head>
<meta charset="utf-8">
<title>Kite Loft – Business Card</title>
<link rel="stylesheet" href="https://fonts.googleapis.com/css2?family=Roboto+Condensed:wght@400;700&family=Open+Sans:wght@400;600&display=swap">
<style>
  :root {
    --backdrop: #d9d4cb;
    --card: #ffffff;
    --brand-blue: #2e94c6;
    --charcoal: #3b3d40;
    --band-grey: #a7a9ac;
    --light-grey: #e6e7e8;
    --text-dark: #444649;
    --white: #ffffff;
  }
  * { box-sizing: border-box; margin: 0; padding: 0; }
  html, body { width: 1200px; height: 682px; overflow: hidden; }
  body {
    background: var(--backdrop);
    display: flex; align-items: center; justify-content: center;
    font-family: "Open Sans", Arial, sans-serif;
  }
  .card {
    position: relative;
    width: 1000px; height: 570px;
    background: var(--card);
    box-shadow: 0 10px 30px rgba(0,0,0,0.18);
    overflow: hidden;
  }
  .card__top-band {
    position: absolute; left: 0; top: 0; width: 100%; height: 26px;
    background: var(--band-grey);
  }
  .card__top-band::after {
    content: ""; position: absolute; left: 0; right: 0; bottom: -10px; height: 10px;
    background: var(--light-grey);
  }
  .brand {
    position: absolute; left: 90px; top: 110px;
    display: flex; align-items: center; gap: 16px;
  }
  .brand__dot {
    width: 58px; height: 58px; border-radius: 50%;
    background: var(--brand-blue);
  }
  .brand__name {
    font-family: "Roboto Condensed", Arial, sans-serif;
    font-weight: 700; font-size: 64px; letter-spacing: 1px;
    color: var(--brand-blue); text-transform: uppercase;
  }
  .name-bar {
    position: absolute; left: 180px; top: 250px; right: 0; height: 64px;
    background: var(--brand-blue);
    display: flex; align-items: center; justify-content: space-between;
    padding: 0 48px 0 110px;
    color: var(--white);
    font-family: "Roboto Condensed", Arial, sans-serif;
  }
  .name-bar__name { font-size: 40px; font-weight: 700; text-transform: uppercase; letter-spacing: 1px; }
  .name-bar__role { font-size: 22px; font-weight: 400; text-transform: uppercase; letter-spacing: 2px; }
  .avatar-tile {
    position: absolute; left: 190px; top: 230px; width: 104px; height: 104px;
    background: var(--charcoal);
    display: flex; align-items: center; justify-content: center;
  }
  .accent-block {
    position: absolute; left: 90px; top: 250px; width: 80px; height: 64px;
    background: var(--brand-blue);
  }
  .contacts {
    position: absolute; left: 330px; top: 350px;
    display: grid; grid-template-columns: 270px 340px; row-gap: 22px; column-gap: 30px;
    color: var(--text-dark); font-size: 21px;
  }
  .contact { display: flex; align-items: center; gap: 14px; }
  .contact svg { flex: none; }
  .address-band {
    position: absolute; left: 0; bottom: 36px; width: 100%; height: 60px;
    background: var(--band-grey);
    display: flex; align-items: center; gap: 14px;
    padding-left: 90px;
    color: var(--white); font-size: 21px;
  }
  .card__bottom-strip {
    position: absolute; left: 0; bottom: 0; width: 100%; height: 24px;
    background: var(--light-grey);
  }
</style>
</head>
<body>
  <main class="card">
    <div class="card__top-band"></div>

    <div class="brand">
      <span class="brand__dot"></span>
      <span class="brand__name">Kite Loft</span>
    </div>

    <div class="accent-block"></div>
    <div class="name-bar">
      <span class="name-bar__name">Corwin T. Aldous</span>
      <span class="name-bar__role">General Manager</span>
    </div>
    <div class="avatar-tile">
      <svg width="44" height="44" viewBox="0 0 44 44" aria-hidden="true">
        <rect x="2" y="2" width="40" height="40" rx="6" fill="var(--white)"/>
        <circle cx="22" cy="17" r="6" fill="var(--charcoal)"/>
        <path d="M10 36c1-7 6-10 12-10s11 3 12 10z" fill="var(--charcoal)"/>
      </svg>
    </div>

    <section class="contacts">
      <div class="contact">
        <svg width="22" height="22" viewBox="0 0 24 24" aria-hidden="true"><path d="M6.6 10.8a15 15 0 006.6 6.6l2.2-2.2c.3-.3.7-.4 1-.2 1.1.4 2.3.6 3.6.6.6 0 1 .4 1 1V20c0 .6-.4 1-1 1A17 17 0 013 4c0-.6.4-1 1-1h3.5c.6 0 1 .4 1 1 0 1.3.2 2.5.6 3.6.1.3 0 .7-.2 1z" fill="var(--text-dark)"/></svg>
        <span>0431 587 904</span>
      </div>
      <div class="contact">
        <svg width="22" height="22" viewBox="0 0 24 24" aria-hidden="true"><rect x="2" y="5" width="20" height="14" rx="1" fill="var(--text-dark)"/><path d="M3 6l9 7 9-7" stroke="var(--white)" stroke-width="1.8" fill="none"/></svg>
        <span>corwin@kiteloftdev.example</span>
      </div>
      <div class="contact">
        <svg width="22" height="22" viewBox="0 0 24 24" aria-hidden="true"><rect x="6" y="2" width="12" height="20" rx="2" fill="none" stroke="var(--text-dark)" stroke-width="2"/><circle cx="12" cy="18.5" r="1.2" fill="var(--text-dark)"/></svg>
        <span>0431 587 905</span>
      </div>
      <div class="contact">
        <svg width="22" height="22" viewBox="0 0 24 24" aria-hidden="true"><circle cx="12" cy="12" r="10" fill="none" stroke="var(--text-dark)" stroke-width="2"/><ellipse cx="12" cy="12" rx="4" ry="10" fill="none" stroke="var(--text-dark)" stroke-width="1.6"/><path d="M2 12h20" stroke="var(--text-dark)" stroke-width="1.6"/></svg>
        <span>www.kiteloftdev.example</span>
      </div>
    </section>

    <div class="address-band">
      <svg width="20" height="26" viewBox="0 0 20 26" aria-hidden="true"><path d="M10 0a9 9 0 00-9 9c0 7 9 17 9 17s9-10 9-17a9 9 0 00-9-9z" fill="var(--white)"/><circle cx="10" cy="9" r="3.4" fill="var(--band-grey)"/></svg>
      <span>42 Harbour Lane, Level 3, Westgate</span>
    </div>
    <div class="card__bottom-strip"></div>
  </main>
</body>
</html>
```